Construction company business card

One side to be the logo with the company name, The other side I would like: (Tomas verbick) Project manager 41 barrow crescent hallam 52917306224783(03) 9703 2428Info@gudeljgroup.comAnd then maybe a couple dot points saying what we do:Construction (commercial & industrial) Civil construction

Anything else please contact me!
Maybe curved st one edge of the card

Target Market(s)

Older clientele

Industry/Entity Type

Construction Company

Contact Information for Business Card

Read above

Colors
3277b5
1b1b1b
9d9d9d

Requirements
Must have
• Use my logo on one side
Nice to have
• Read above
Should not have
• Read above

```html
<!DOCTYPE html>
<html lang="en">
<head>
<meta charset="utf-8">
<title>Stonefield Property Group – Business Card</title>
<link href="https://fonts.googleapis.com/css2?family=Roboto:wght@400;500;700;900&display=swap" rel="stylesheet">
<style>
  :root {
    --brand-blue: #2f5f91;
    --brand-blue-text: #2d5a8c;
    --ink: #1b1b1b;
    --steel: #9d9d9d;
    --paper: #f1f1f1;
    --backdrop: #bdbdbd;
    --on-blue: #ffffff;
    --on-blue-soft: #d9e3ee;
  }
  * { box-sizing: border-box; margin: 0; padding: 0; }
  html, body {
    width: 1200px; height: 576px; overflow: hidden;
    background: var(--backdrop);
    font-family: "Roboto", Arial, sans-serif;
  }
  .canvas { position: relative; width: 1200px; height: 576px; }

  .card {
    position: absolute; overflow: hidden;
    border-radius: 0 32px 0 32px;
    box-shadow: 0 3px 6px rgba(0,0,0,0.25);
  }

  /* Front */
  .card--front {
    left: 80px; top: 138px; width: 486px; height: 294px;
    background: var(--brand-blue);
  }
  .card--front .decor-circle {
    position: absolute; left: 40px; top: 10px;
    width: 300px; height: 300px; border-radius: 50%;
    border: 34px solid rgba(255,255,255,0.08);
  }
  .front-name {
    position: absolute; left: 0; width: 456px; top: 112px;
    text-align: center; color: var(--on-blue); font-weight: 900;
  }
  .front-name__main { display: block; font-size: 40px; letter-spacing: 1px; line-height: 1; }
  .front-name__sub { display: block; font-size: 15px; letter-spacing: 5px; margin-top: 4px; }
  .front-services {
    position: absolute; left: 0; width: 456px; top: 262px;
    text-align: center; font-size: 13px; color: var(--on-blue-soft);
  }

  /* Back */
  .card--back {
    left: 602px; top: 160px; width: 480px; height: 270px;
    background: linear-gradient(135deg, #f7f7f7, var(--paper));
  }
  .card--back .decor-circle {
    position: absolute; left: 250px; top: 20px;
    width: 250px; height: 250px; border-radius: 50%;
    border: 30px solid rgba(0,0,0,0.04);
  }
  .back-name {
    position: absolute; left: 96px; top: 28px;
    display: flex; align-items: center; gap: 12px;
    color: var(--brand-blue-text); font-weight: 900;
  }
  .back-name__mark { width: 40px; height: 40px; border-radius: 50%; background: var(--brand-blue); flex: none; }
  .back-name__main { display: block; font-size: 30px; letter-spacing: 1px; line-height: 1; }
  .back-name__sub { display: block; font-size: 12px; letter-spacing: 4px; margin-top: 3px; }

  .person {
    position: absolute; right: 245px; top: 131px; text-align: right;
    color: var(--ink); font-size: 13px;
  }
  .person__name { font-size: 17px; font-weight: 700; color: var(--brand-blue-text); }
  .person__role { margin-top: 2px; }
  .person__address { margin-top: 9px; }

  .contact-list {
    position: absolute; left: 262px; top: 132px; list-style: none;
    font-size: 13px; color: var(--ink);
  }
  .contact-list li { display: flex; align-items: center; gap: 10px; height: 19px; }
  .contact-list svg { width: 11px; height: 11px; fill: var(--brand-blue); flex: none; }

  .back-services {
    position: absolute; left: 0; width: 480px; top: 223px;
    text-align: center; font-size: 12px; color: var(--brand-blue-text);
  }
  .back-band {
    position: absolute; left: 240px; right: 0; bottom: 0; height: 12px;
    background: var(--brand-blue);
  }
</style>
</head>
<body>
<main class="canvas">

  <section class="card card--front" aria-label="Card front">
    <div class="decor-circle" aria-hidden="true"></div>
    <h1 class="front-name">
      <span class="front-name__main">STONEFIELD</span>
      <span class="front-name__sub">PROPERTY GROUP</span>
    </h1>
    <p class="front-services">Construction (Commercial &amp; Industrial) Civil Construction</p>
  </section>

  <section class="card card--back" aria-label="Card back">
    <div class="decor-circle" aria-hidden="true"></div>
    <div class="back-name">
      <span class="back-name__mark" aria-hidden="true"></span>
      <span>
        <span class="back-name__main">STONEFIELD</span>
        <span class="back-name__sub">PROPERTY GROUP</span>
      </span>
    </div>

    <div class="person">
      <p class="person__name">Tomas Verbick</p>
      <p class="person__role">Project Manager</p>
      <p class="person__address">41 Barrow Crescent Hallam 5291</p>
    </div>

    <ul class="contact-list">
      <li>
        <svg viewBox="0 0 12 12" aria-hidden="true"><path d="M1 4c0-2 1-3 5-3s5 1 5 3H8.5V3h-5v1z"/><rect x="2" y="5" width="8" height="6" rx="1"/></svg>
        <span>(73) 0622 4783</span>
      </li>
      <li>
        <svg viewBox="0 0 12 12" aria-hidden="true"><path d="M0 2h12v1L6 7 0 3z"/><path d="M0 4.5l6 4 6-4V10H0z"/></svg>
        <span>(03) 9418 6573</span>
      </li>
      <li>
        <svg viewBox="0 0 12 12" aria-hidden="true"><circle cx="6" cy="6" r="5.5"/></svg>
        <span>info@verbickgroup.com</span>
      </li>
    </ul>

    <p class="back-services">Construction (Commercial &amp; Industrial) Civil Construction</p>
    <div class="back-band" aria-hidden="true"></div>
  </section>

</main>
</body>
</html>
```